BLS Business Card 2018

Larkmere Chiropractic. We have two locations that we want to advertise on the same card. Brightvale OrthoCore campus address: 3815 Pellham Dr., Suite 240, Flowood, MS 39417. Madison address: 246 Willowmere Dr., Building D., Madison, MS 39284. website: www.drlarkmere-example.com. o:(601)555-0147 f:(601)555-0183

Target Market(s)

Health care decision makers: primary care doctors and mothers

Contact Information for Business Card

I have no idea; up for any suggestions and I'd do much better picking from examples versus describing what I'm looking for. We are in a very high end location and would like the cards to look really sharp.

Requirements
Must have
• My name, Martin R Belvane, D.C.

```html
<!DOCTYPE html>
<html lang="en">
<head>
<meta charset="utf-8">
<title>Larkmere Chiropractic Business Card</title>
<link href="https://fonts.googleapis.com/css2?family=Alegreya:wght@400;500;700&display=swap" rel="stylesheet">
<style>
  :root {
    --backdrop: #3a3b3d;
    --card-dark: #1f2022;
    --logo-emboss: #2d2f32;
    --band-blue: #0f5d80;
    --name-blue: #1a86c8;
    --logo-blue: #125c80;
    --accent-teal: #3bb3c9;
    --paper: #fafafa;
    --ink-light: #f2f2f2;
    --placeholder-dark: #26282b;
    --placeholder-light: #e6e9ec;
  }
  * { margin: 0; padding: 0; box-sizing: border-box; }
  html, body { width: 799px; height: 1200px; overflow: hidden; }
  body {
    background: var(--backdrop);
    font-family: "Alegreya", Georgia, serif;
    color: var(--ink-light);
    position: relative;
  }
  .card {
    position: absolute;
    left: 60px;
    width: 680px;
    height: 390px;
    border-radius: 26px;
    background: var(--card-dark);
    overflow: hidden;
  }
  .card--front { top: 130px; }
  .card--back { top: 680px; }

  /* front */
  .front-figure {
    position: absolute; left: 190px; top: 40px;
    width: 90px; height: 110px;
    background: var(--placeholder-dark);
    border-radius: 8px;
  }
  .front-wordmark {
    position: absolute; left: 290px; top: 52px;
    color: var(--logo-emboss);
    font-weight: 500;
    line-height: 0.95;
    letter-spacing: 1px;
    text-transform: uppercase;
  }
  .front-wordmark .line-1 { display: block; font-size: 52px; }
  .front-wordmark .line-2 { display: block; font-size: 38px; }
  .address-band {
    position: absolute; left: 0; top: 185px;
    width: 100%; height: 108px;
    background: var(--band-blue);
  }
  .campus-pill {
    position: absolute; left: 235px; top: 160px;
    width: 220px; height: 46px;
    border: 2px solid var(--ink-light);
    border-radius: 23px;
    background: var(--card-dark);
    font-weight: 700; font-size: 19px;
    display: flex; align-items: center; justify-content: center;
  }
  .address {
    position: absolute;
    font-size: 17px; line-height: 1.2;
    padding-left: 22px;
  }
  .address svg { position: absolute; left: 0; top: 3px; }
  .address--flowood { left: 50px; top: 212px; }
  .address--madison { left: 372px; top: 232px; }
  .band-divider {
    position: absolute; left: 350px; top: 228px;
    width: 1px; height: 50px;
    background: rgba(255,255,255,0.4);
  }
  .front-web {
    position: absolute; left: 0; top: 318px; width: 100%;
    display: flex; align-items: center; justify-content: center; gap: 22px;
    font-size: 19px;
  }
  .front-web .rule { width: 70px; height: 2px; background: var(--ink-light); }

  /* back */
  .back-shape { position: absolute; inset: 0; }
  .person-name {
    position: absolute; left: 42px; top: 36px;
    color: var(--name-blue); font-size: 27px; font-weight: 500;
  }
  .person-title { position: absolute; left: 44px; top: 72px; font-size: 12px; }
  .contact-list {
    position: absolute; left: 40px; top: 250px;
    list-style: none; font-size: 15px; line-height: 23px;
  }
  .contact-list li { display: flex; align-items: center; gap: 10px; white-space: nowrap; }
  .contact-list svg { flex: none; }
  .back-figure {
    position: absolute; left: 500px; top: 92px;
    width: 110px; height: 120px;
    background: var(--placeholder-light);
    border-radius: 10px;
  }
  .back-wordmark {
    position: absolute; left: 432px; top: 222px;
    color: var(--logo-blue); font-weight: 500;
    text-transform: uppercase; line-height: 0.95; letter-spacing: 1px;
  }
  .back-wordmark .line-1 { display: block; font-size: 42px; }
  .back-wordmark .line-2 { display: block; font-size: 30px; }
</style>
</head>
<body>

<section class="card card--front" aria-label="Card front">
  <div class="front-figure" role="img" aria-label="Embossed spine illustration area"></div>
  <div class="front-wordmark"><span class="line-1">Larkmere</span><span class="line-2">Chiropractic</span></div>

  <div class="address-band"></div>
  <div class="campus-pill">OrthoCore Campus</div>

  <p class="address address--flowood">
    <svg width="12" height="16" viewBox="0 0 12 16"><path d="M6 0a6 6 0 0 0-6 6c0 4.5 6 10 6 10s6-5.5 6-10a6 6 0 0 0-6-6zm0 8.5A2.5 2.5 0 1 1 6 3.5a2.5 2.5 0 0 1 0 5z" fill="#fff"/></svg>
    3815 Pellham Dr., Suite 240,<br>Flowood, MS 39417
  </p>
  <div class="band-divider"></div>
  <p class="address address--madison">
    <svg width="12" height="16" viewBox="0 0 12 16"><path d="M6 0a6 6 0 0 0-6 6c0 4.5 6 10 6 10s6-5.5 6-10a6 6 0 0 0-6-6zm0 8.5A2.5 2.5 0 1 1 6 3.5a2.5 2.5 0 0 1 0 5z" fill="#fff"/></svg>
    246 Willowmere Dr., Building D.,<br>Madison, MS 39284
  </p>

  <p class="front-web"><span class="rule"></span>www.drlarkmere-example.com<span class="rule"></span></p>
</section>

<section class="card card--back" aria-label="Card back">
  <svg class="back-shape" width="680" height="390" viewBox="0 0 680 390">
    <path d="M466 0 C 400 100 362 250 340 390 L680 390 L680 0 Z" fill="var(--accent-teal)"/>
    <path d="M480 0 C 414 100 376 250 356 390 L680 390 L680 0 Z" fill="var(--paper)"/>
  </svg>

  <h1 class="person-name">Martin R Belvane, D.C.</h1>
  <p class="person-title">Managing Director</p>

  <ul class="contact-list">
    <li>
      <svg width="13" height="13" viewBox="0 0 14 14"><path d="M3 1l2.5 3-1.5 1.5a8 8 0 0 0 4.5 4.5L10 8.5 13 11l-1.5 2C6 13 1 8 1 2.5z" fill="var(--name-blue)"/></svg>
      (601)555-0147
    </li>
    <li>
      <svg width="13" height="13" viewBox="0 0 14 14"><rect x="3" y="1" width="8" height="4" fill="var(--name-blue)"/><rect x="1" y="5" width="12" height="6" rx="1" fill="var(--name-blue)"/><rect x="3" y="9" width="8" height="4" fill="var(--name-blue)"/></svg>
      (601)555-0183
    </li>
    <li>
      <svg width="13" height="13" viewBox="0 0 14 14"><rect x="1" y="3" width="12" height="8" fill="var(--name-blue)"/><path d="M1 3l6 5 6-5" stroke="var(--card-dark)" stroke-width="1.2" fill="none"/></svg>
      m.r.belvane@drlarkmere-example.com
    </li>
    <li>
      <svg width="13" height="13" viewBox="0 0 14 14"><circle cx="7" cy="7" r="6" fill="var(--name-blue)"/><path d="M1 7h12M7 1c-3 3-3 9 0 12M7 1c3 3 3 9 0 12" stroke="var(--card-dark)" stroke-width="1" fill="none"/></svg>
      www.drlarkmere-example.com
    </li>
  </ul>

  <div class="back-figure" role="img" aria-label="Line illustration of a human back and spine"></div>
  <div class="back-wordmark"><span class="line-1">Larkmere</span><span class="line-2">Chiropractic</span></div>
</section>

</body>
</html>
```